Market Research firm needs updated business cards with new logo

We need the logo to be included somewhere on the card (attached). We would also like the phrases "Independent, Objective, Comprehensive" and "Research You Can Trust" somewhere on the card. Front or back. Our colors are hex codes 6075a7, e48d25 and 5a5b5b. Though you are certainly not limited to those shades, whatever you produce should coordinate with them. I have also attached our favicon. Feel free to use it in your design, but please do not use it to replace the full logo.

Contact Information for Business Card

see project description

Font styles to use
Other font styles liked:
• Open Sans

Requirements
Must have
• the logo
• We use Open Sans font

```html
<!DOCTYPE html>
<html lang="en">
<head>
<meta charset="utf-8">
<title>Corvane Research – Business Cards</title>
<link href="https://fonts.googleapis.com/css2?family=Open+Sans:wght@400;600&family=Work+Sans:wght@400;500&display=swap" rel="stylesheet">
<style>
  :root {
    --stage: #d6d7d8;
    --slate: #6b7a8b;
    --orange: #e48d25;
    --ink: #5f6b78;
    --paper: #ffffff;
  }
  * { box-sizing: border-box; margin: 0; padding: 0; }
  html, body { width: 1200px; height: 930px; overflow: hidden; }
  body { background: var(--stage); font-family: "Open Sans", sans-serif; position: relative; }

  .card {
    position: absolute;
    width: 560px;
    height: 320px;
    border-radius: 20px;
    overflow: hidden;
  }

  /* Front */
  .card--front { left: 60px; top: 90px; background: var(--slate); }
  .brand {
    position: absolute;
    display: flex; align-items: center; gap: 12px;
    font-weight: 400;
    letter-spacing: -0.5px;
  }
  .brand__dot { width: 20px; height: 20px; border-radius: 50%; background: var(--orange); flex: none; }
  .card--front .brand {
    left: 0; right: 0; top: 108px; justify-content: center;
    font-size: 42px; color: var(--paper);
  }
  .tagline {
    position: absolute; left: 0; right: 0; top: 210px;
    text-align: center; color: var(--paper);
    font-family: "Work Sans", sans-serif; font-size: 14px; line-height: 1.45; letter-spacing: 0.6px;
  }

  /* Back */
  .card--back { left: 580px; top: 520px; background: var(--paper); }
  .name-band { position: absolute; left: 0; top: 62px; }
  .name-band__text { position: absolute; left: 26px; top: 66px; color: var(--paper); }
  .person-name { font-family: "Work Sans", sans-serif; font-weight: 500; font-size: 20px; letter-spacing: 0.5px; line-height: 1.1; }
  .person-role { font-family: "Work Sans", sans-serif; font-size: 14px; letter-spacing: 0.4px; }
  .card--back .brand { left: 232px; top: 22px; font-size: 30px; color: var(--ink); gap: 9px; }
  .card--back .brand__dot { width: 15px; height: 15px; }

  .address {
    position: absolute; right: 30px; top: 152px; text-align: right;
    font-family: "Work Sans", sans-serif; font-size: 14px; line-height: 1.5; color: var(--ink); letter-spacing: 0.3px;
  }
  .contact-list { position: absolute; left: 30px; top: 236px; list-style: none; }
  .contact-list li {
    display: flex; align-items: center; gap: 9px;
    font-family: "Work Sans", sans-serif; font-size: 14px; line-height: 1.55; color: var(--ink); letter-spacing: 0.3px;
  }
  .contact-list svg { width: 11px; height: 11px; flex: none; }
</style>
</head>
<body>

<section class="card card--front">
  <div class="brand"><span class="brand__dot"></span><span>Corvane Research</span></div>
  <p class="tagline">Independent - Objective - Comprehensive<br>Research You Can Trust</p>
</section>

<section class="card card--back">
  <svg class="name-band" width="250" height="56" viewBox="0 0 250 56">
    <polygon points="0,0 250,0 214,56 0,56" fill="var(--slate)"/>
  </svg>
  <div class="name-band__text" style="top:70px">
    <div class="person-name">DANIEL HART</div>
    <div class="person-role">Director</div>
  </div>

  <div class="brand"><span class="brand__dot"></span><span>Corvane Research</span></div>

  <address class="address" style="font-style:normal">
    210 Linden Street<br>Fairview, OR 97024
  </address>

  <ul class="contact-list">
    <li>
      <svg viewBox="0 0 12 12"><path d="M2.5 1 L4.5 1 L5.2 3.6 L4 4.6 C4.6 6 6 7.4 7.4 8 L8.4 6.8 L11 7.5 L11 9.5 C11 10.3 10.3 11 9.5 11 C5 11 1 7 1 2.5 C1 1.7 1.7 1 2.5 1 Z" fill="var(--orange)"/></svg>
      555 214-3087
    </li>
    <li>
      <svg viewBox="0 0 12 12"><rect x="1" y="2.5" width="10" height="7" rx="1" fill="none" stroke="var(--orange)" stroke-width="1.3"/><path d="M1.5 3 L6 6.5 L10.5 3" fill="none" stroke="var(--orange)" stroke-width="1.3"/></svg>
      info@corvaneresearch.com
    </li>
    <li>
      <svg viewBox="0 0 12 12"><circle cx="6" cy="6" r="5" fill="none" stroke="var(--orange)" stroke-width="1.2"/><ellipse cx="6" cy="6" rx="2.2" ry="5" fill="none" stroke="var(--orange)" stroke-width="1"/><line x1="1" y1="6" x2="11" y2="6" stroke="var(--orange)" stroke-width="1"/></svg>
      www.corvaneresearch.com
    </li>
  </ul>
</section>

</body>
</html>
```